Creative, fresh business card design for Ripplecraft Facades

We need a fresh, creative business card design for Ripplecraft Facades. We are the manufacturer of Ripplecraft Facades in Australia. Wall panels are 2400 x 1200mm panels made from MDF and feature 3D patterns on the face of the panel. The colours to be used are green, silver/grey and white RGB
Red 187
Green 207
Blue 65.

An idea is to possibly use a watermark of one of our designs as a background (like on the "Grids" design on the left hand side of page 2 of our brochure).

Target Market(s)

Interior designers, architects, builders and home renovators

Industry/Entity Type

Business

Contact Information for Business Card

Details to go on the card are:
Our logo (attached),
Slogan: "Decorative panels for interiors and exteriors",
Contact name,
Position,
Mobile phone number,
Business address,
Business phone,
Business fax,
Website and
Email address.

I have attached a few images of our panels and our brochure for reference.

The colours of the business card should feature our logo colours which are: RGB
Red 187
Green 207
Blue 65

Requirements
Must have
• Very modern fonts and design. Some of the designs shown especially the "Prisms" design which is a popular design.
Nice to have
• Creative but simple design. Very contemporary.
Should not have
• Anything ornate or old fashioned.

```html
<!DOCTYPE html>
<html lang="en">
<head>
<meta charset="utf-8">
<title>Ripplecraft Facades – Business Card</title>
<link rel="stylesheet" href="https://fonts.googleapis.com/css2?family=Roboto:wght@300;400;700&display=swap">
<style>
  :root {
    --stage: #231f20;
    --brand-green: rgb(187, 207, 65);
    --brand-grey: #929497;
    --paper: #ffffff;
    --ink: #231f20;
    --pattern-light: #fbfbfb;
    --pattern-shade: #e9e9ea;
  }
  * { box-sizing: border-box; margin: 0; padding: 0; }
  html, body {
    width: 1200px; height: 1071px; overflow: hidden;
    background: var(--stage);
    font-family: "Roboto", Arial, sans-serif;
  }
  .stage { position: relative; width: 1200px; height: 1071px; }

  .side-label {
    position: absolute; color: var(--paper);
    font-weight: 700; font-size: 31px; letter-spacing: 0.5px;
  }
  .side-label--front { left: 132px; top: 306px; }
  .side-label--back  { left: 152px; top: 776px; }

  .card {
    position: absolute; left: 298px; width: 684px; height: 416px;
    background: var(--paper); overflow: hidden;
  }
  .card--front { top: 61px; }
  .card--back  { top: 551px; }

  .card__texture {
    position: absolute; inset: 0;
    background: linear-gradient(160deg, var(--pattern-light) 0%, var(--pattern-shade) 45%, var(--pattern-light) 70%, var(--pattern-shade) 100%);
  }

  /* Front */
  .brand {
    position: absolute; left: 0; right: 0; top: 96px;
    display: flex; align-items: center; justify-content: center; gap: 18px;
  }
  .brand__mark { width: 64px; height: 64px; background: var(--brand-green); }
  .brand__name { font-weight: 300; font-size: 46px; color: var(--brand-grey); }
  .slogan {
    position: absolute; left: 0; right: 0; top: 284px;
    text-align: center; font-weight: 300; font-size: 25px; color: var(--ink);
  }
  .footer-band {
    position: absolute; left: 0; right: 0; bottom: 0; height: 68px; display: flex;
    box-shadow: 0 -6px 10px rgba(0,0,0,0.12);
  }
  .social {
    width: 276px; background: var(--brand-green);
    display: flex; align-items: center; padding-left: 24px;
  }
  .social__item {
    width: 60px; height: 44px; display: flex; align-items: center; justify-content: center;
    border-right: 1px solid rgba(255,255,255,0.8);
  }
  .social__item:last-child { border-right: none; }
  .social__dot { width: 22px; height: 22px; border-radius: 50%; background: var(--paper); }
  .website {
    flex: 1; background: var(--brand-grey); color: var(--paper);
    display: flex; align-items: center; justify-content: center;
    font-size: 22px; font-weight: 400;
  }

  /* Back */
  .holder {
    position: absolute; left: 210px; right: 0; top: 86px; height: 86px;
    background: var(--brand-green); color: var(--paper); padding: 17px 0 0 30px;
  }
  .holder__name { font-weight: 700; font-size: 25px; letter-spacing: 0.6px; }
  .holder__role { font-weight: 300; font-size: 18px; margin-top: 4px; }

  .contacts { position: absolute; left: 0; right: 0; top: 173px; list-style: none; }
  .contact { display: flex; align-items: center; height: 33px; }
  .contact__band {
    width: 210px; height: 100%; display: flex; align-items: center; justify-content: flex-end;
    padding-right: 10px;
  }
  .contact:nth-child(odd) .contact__band { background: var(--brand-grey); }
  .contact:nth-child(even) .contact__band { background: var(--brand-green); }
  .contact__icon { width: 24px; height: 24px; fill: none; stroke: var(--paper); stroke-width: 1.5; }
  .contact__text { padding-left: 10px; font-size: 17px; font-weight: 300; color: var(--ink); }
</style>
</head>
<body>
<main class="stage">
  <span class="side-label side-label--front">FRONT</span>
  <span class="side-label side-label--back">BACK</span>

  <section class="card card--front">
    <div class="card__texture" role="img" aria-label="Faint background texture of embossed pyramid wall panels"></div>
    <div class="brand">
      <span class="brand__mark"></span>
      <span class="brand__name">Ripplecraft Facades</span>
    </div>
    <p class="slogan">Decorative panels for interiors and exteriors</p>
    <div class="footer-band">
      <div class="social" aria-label="Social channels">
        <span class="social__item"><span class="social__dot"></span></span>
        <span class="social__item"><span class="social__dot"></span></span>
        <span class="social__item"><span class="social__dot"></span></span>
        <span class="social__item"><span class="social__dot"></span></span>
      </div>
      <div class="website">www.ripplecraftfacades.com.au</div>
    </div>
  </section>

  <section class="card card--back">
    <div class="card__texture" role="img" aria-label="Faint background texture of embossed pyramid wall panels"></div>
    <div class="holder">
      <p class="holder__name">MARLA JEFFCOTT</p>
      <p class="holder__role">OWNER,</p>
    </div>
    <ul class="contacts">
      <li class="contact">
        <span class="contact__band">
          <svg class="contact__icon" viewBox="0 0 24 24"><rect x="6.5" y="1.5" width="11" height="21" rx="1.5"/><line x1="6.5" y1="5" x2="17.5" y2="5"/><line x1="6.5" y1="19" x2="17.5" y2="19"/></svg>
        </span>
        <span class="contact__text">04 321 765 980</span>
      </li>
      <li class="contact">
        <span class="contact__band">
          <svg class="contact__icon" viewBox="0 0 24 24"><path d="M12 22.5s-7-7.5-7-13a7 7 0 0 1 14 0c0 5.5-7 13-7 13z"/><circle cx="12" cy="9.5" r="3"/></svg>
        </span>
        <span class="contact__text">14 Alder Lane, Kestrel Vale NSW 2190</span>
      </li>
      <li class="contact">
        <span class="contact__band">
          <svg class="contact__icon" viewBox="0 0 24 24"><path d="M2 9c0-3 4-5 10-5s10 2 10 5l-4 1-1-3H7L6 10z"/><path d="M5 12h14l1 8H4z"/><circle cx="12" cy="16" r="2.5"/></svg>
        </span>
        <span class="contact__text">02 5550 1847</span>
      </li>
      <li class="contact">
        <span class="contact__band">
          <svg class="contact__icon" viewBox="0 0 24 24"><rect x="2" y="7" width="5" height="15" rx="1"/><rect x="7" y="4" width="15" height="18"/><line x1="10" y1="8" x2="19" y2="8"/><line x1="10" y1="12" x2="19" y2="12"/><line x1="10" y1="15" x2="19" y2="15"/><line x1="10" y1="18" x2="19" y2="18"/></svg>
        </span>
        <span class="contact__text">02 5550 1862</span>
      </li>
      <li class="contact">
        <span class="contact__band">
          <svg class="contact__icon" viewBox="0 0 24 24"><circle cx="12" cy="12" r="4"/><path d="M16 8v5.5a2.5 2.5 0 0 0 5 0V12a9 9 0 1 0-3.5 7.1"/></svg>
        </span>
        <span class="contact__text">sales@ripplecraftfacades.com.au</span>
      </li>
    </ul>
  </section>
</main>
</body>
</html>
```